Business Card Design Project

After recently finishing a design project for the company logo using markbazaar, it's now time for a business card. Attached to this is the logo.

The requirements for the business card are pretty straightforward:

- A clean, uncomplicated look
- Consistent usage of fonts
- Designs for both single sided and double sided cards
- A modern layout with preferably space to refer to social media accounts and/or downloadable vcards through a qr code
- consistent application of the company colour scheme: red/white. Hex codes for exact colour can be provided

Thanks!

```html
<!DOCTYPE html>
<html lang="en">
<head>
<meta charset="utf-8">
<title>Kiln Row Staffing – Business Card</title>
<link rel="stylesheet" href="https://fonts.googleapis.com/css2?family=Source+Sans+3:ital,wght@0,400;0,600;0,700;1,700&display=swap">
<style>
  :root {
    --bg: #e9e6e2;
    --card: #ffffff;
    --ink: #231f20;
    --text: #333333;
    --brand-red: #e31e26;
    --shadow: rgba(0, 0, 0, 0.28);
  }
  * { margin: 0; padding: 0; box-sizing: border-box; }
  html, body {
    width: 960px;
    height: 1200px;
    overflow: hidden;
    background: var(--bg);
    font-family: "Source Sans 3", "Myriad Pro", Arial, sans-serif;
  }
  .canvas { position: relative; width: 960px; height: 1200px; }

  .card {
    position: absolute;
    width: 840px;
    height: 480px;
    background: var(--card);
    border-radius: 32px;
    box-shadow: 4px 6px 10px var(--shadow);
  }
  .card--front { left: 58px; top: 70px; }
  .card--back  { left: 60px; top: 638px; }

  .wordmark {
    position: absolute;
    left: 0;
    right: 0;
    display: flex;
    align-items: center;
    justify-content: center;
    gap: 22px;
  }
  .card--front .wordmark { top: 128px; }
  .card--back .wordmark  { top: 196px; }

  .wordmark__square {
    width: 58px;
    height: 58px;
    background: var(--brand-red);
  }
  .wordmark__name {
    font-weight: 600;
    font-size: 68px;
    line-height: 1;
    letter-spacing: -0.5px;
    color: var(--ink);
  }

  .contact {
    position: absolute;
    left: 0;
    right: 0;
    top: 320px;
    text-align: center;
    color: var(--text);
    font-size: 19px;
    line-height: 1.4;
  }
  .contact__person { font-size: 19px; margin-bottom: 14px; }
  .contact__name { font-weight: 700; font-size: 25px; }
  .contact__label { font-weight: 700; font-style: italic; }
  .contact__sep { margin: 0 6px; }
  .contact__line { margin-bottom: 4px; }
  .contact__line--phone { margin-bottom: 8px; }
</style>
</head>
<body>
<main class="canvas">
  <section class="card card--front" aria-label="Business card front">
    <div class="wordmark">
      <span class="wordmark__square" aria-hidden="true"></span>
      <span class="wordmark__name">Kiln Row Staffing</span>
    </div>
    <div class="contact">
      <p class="contact__person"><span class="contact__name">Your Name,</span> Designation</p>
      <p class="contact__line contact__line--phone"><span class="contact__label">t</span> : 123-123-1234</p>
      <p class="contact__line">
        <span class="contact__label">e</span> : info@yourwebsite.com<span class="contact__sep">|</span><span class="contact__label">w</span> : www.kilnrow.com
      </p>
      <p class="contact__line">1234, Street Name, District, City, Country Code.</p>
    </div>
  </section>

  <section class="card card--back" aria-label="Business card back">
    <div class="wordmark">
      <span class="wordmark__square" aria-hidden="true"></span>
      <span class="wordmark__name">Kiln Row Staffing</span>
    </div>
  </section>
</main>
</body>
</html>
```